BRIGHT RIVER POWER.

I'd like my business logo.
contact name: Dennis Halvorsen
phone:0438759164
email: info@brightriverpower.net.au
website: www.brightriverpower.net.au

services:
solar
battery storage
LED lighting
energy saving solutions
general electrical
I'd like the design to look professional

Target Market(s)

Everyone

Industry/Entity Type

Business

Contact Information for Business Card

as described above

Requirements
Must have
• Id like the colours and the design to work well with my logo.

```html
<!DOCTYPE html>
<html lang="en">
<head>
<meta charset="utf-8">
<title>Bright River Power – Business Card</title>
<link rel="stylesheet" href="https://fonts.googleapis.com/css2?family=Arimo:wght@400;700&display=swap">
<style>
  :root {
    --backdrop: #2b2b2b;
    --card-white: #ffffff;
    --card-white-shade: #ececec;
    --green-light: #4fae5a;
    --green-mid: #44a04c;
    --green-dark: #5c9a2a;
    --brand-green: #3f9a3f;
    --accent-orange: #e6890f;
    --ink-dark: #1d1d1d;
    --ink-light: #ffffff;
    --dot-red: #d8322a;
  }
  * { box-sizing: border-box; margin: 0; padding: 0; }
  html, body {
    width: 1200px; height: 997px; overflow: hidden;
    background: var(--backdrop);
    font-family: "Arimo", Arial, sans-serif;
  }
  .canvas {
    position: relative; width: 1200px; height: 997px;
    display: flex; align-items: center; justify-content: center;
  }
  .business-card {
    position: relative; width: 900px; height: 514px;
    border-radius: 26px; overflow: hidden;
    display: flex;
    box-shadow: 0 18px 40px rgba(0,0,0,.5);
  }
  .brand-side {
    position: relative; width: 450px; height: 100%;
    background: linear-gradient(160deg, var(--card-white) 40%, var(--card-white-shade));
    display: flex; flex-direction: column; align-items: center;
  }
  .brand-mark {
    margin-top: 170px;
    display: flex; align-items: center; gap: 16px;
  }
  .brand-mark .mark-dot {
    width: 46px; height: 46px; border-radius: 50%;
    background: var(--brand-green);
  }
  .brand-mark .brand-name {
    font-weight: 700; font-size: 34px; letter-spacing: .5px;
    color: var(--brand-green); line-height: 1;
  }
  .services {
    position: absolute; bottom: 52px; left: 0; right: 0;
    text-align: center; color: var(--brand-green);
    font-size: 21px; line-height: 1.4;
  }
  .services .services-title {
    color: var(--accent-orange); font-weight: 700; font-size: 22px;
  }
  .services .sep { color: var(--dot-red); padding: 0 4px; }
  .divider {
    width: 6px; height: 100%; background: var(--accent-orange);
  }
  .contact-side {
    position: relative; flex: 1; height: 100%;
    background: linear-gradient(170deg, var(--green-light) 0%, var(--green-mid) 50%, var(--green-dark) 100%);
    color: var(--ink-light);
  }
  .name-tag {
    position: absolute; top: 26px; left: 0;
    display: flex; align-items: flex-start; gap: 12px;
  }
  .name-tag .pointer { width: 20px; height: 40px; }
  .name-tag .person-name {
    color: var(--ink-dark); font-weight: 700; font-size: 22px; line-height: 1.1;
  }
  .name-tag .person-role {
    color: var(--ink-light); font-size: 16px;
  }
  .contact-list {
    position: absolute; left: 50px; bottom: 66px;
    list-style: none; font-size: 21px;
  }
  .contact-list li {
    display: flex; align-items: center; gap: 22px; margin-top: 16px;
  }
  .contact-list .icon {
    width: 26px; height: 26px; border-radius: 50%;
    background: var(--ink-light);
    display: flex; align-items: center; justify-content: center;
  }
  .contact-list .icon svg { width: 14px; height: 14px; }
</style>
</head>
<body>
<main class="canvas">
  <article class="business-card">
    <section class="brand-side">
      <div class="brand-mark">
        <span class="mark-dot"></span>
        <span class="brand-name">BRIGHT RIVER POWER</span>
      </div>
      <div class="services">
        <p class="services-title">Our Services</p>
        <p>Solar<span class="sep">•</span>LED lighting</p>
        <p>Battery storage<span class="sep">•</span>Energy saving solutions</p>
      </div>
    </section>
    <div class="divider"></div>
    <section class="contact-side">
      <div class="name-tag">
        <svg class="pointer" viewBox="0 0 20 40"><polygon points="0,0 20,20 0,40" fill="#ffffff"/></svg>
        <div>
          <p class="person-name">Dennis Halvorsen</p>
          <p class="person-role">President</p>
        </div>
      </div>
      <ul class="contact-list">
        <li>
          <span class="icon"><svg viewBox="0 0 24 24"><path fill="#44a04c" d="M6.6 10.8a15 15 0 0 0 6.6 6.6l2.2-2.2a1 1 0 0 1 1-.25 11.4 11.4 0 0 0 3.6.6 1 1 0 0 1 1 1V20a1 1 0 0 1-1 1A17 17 0 0 1 3 4a1 1 0 0 1 1-1h3.5a1 1 0 0 1 1 1c0 1.25.2 2.45.6 3.6a1 1 0 0 1-.25 1z"/></svg></span>
          0438759164
        </li>
        <li>
          <span class="icon"><svg viewBox="0 0 24 24"><rect x="2" y="5" width="20" height="14" rx="2" fill="#44a04c"/><path d="M2 6l10 7 10-7" stroke="#ffffff" stroke-width="2" fill="none"/></svg></span>
          info@brightriverpower.net.au
        </li>
        <li>
          <span class="icon"><svg viewBox="0 0 24 24"><circle cx="12" cy="12" r="9" fill="none" stroke="#44a04c" stroke-width="2.5"/><path d="M3 12h18M12 3c3 3 3 15 0 18M12 3c-3 3-3 15 0 18" stroke="#44a04c" stroke-width="2" fill="none"/></svg></span>
          www.brightriverpower.net.au
        </li>
      </ul>
    </section>
  </article>
</main>
</body>
</html>
```